New B2C website design to help dads be better dads

DadHarbor is a website to help dads be the “best dad you can be.”

We require our website to be designed into a PSD format, no coding necessary.

The general concept is a two-page design. The first page is the login page, the second page is the home page. Once at the home page, rather than navigating to and from different pages, the user will push and pull through different visual and functional layers of the hierarchy. In theory, this should add to the user experience by having a visual anchor of where they are (through layered pagination) as well as improving loading times since the new information should only be a delta in data load versus a brand new page load.

The general look-and-feel we are going for is clean, simple, minimal. This means that the winning design will show us a good eye for web-optimized typography, good use of white (negative) space, and good use of a visually pleasing grid.

We require a total of 6 page "views" plus the landing page. We note that many of the views are similar to one another.
Landing page
Milestone view
Task view
Content view, articles
Content view, products
Search view
What's new view

Please review all of the additional information provided as well as the attachments for examples.

We provide the following websites as good references for:

Typography:
http://example-kelvorn.com/journal/

Use of white space:
http://www.trenvaskit.com/
http://moldrefin.com/

Example for “scrolling” page concept as well as good balance of color, typography, and white space:
http://www.qorbitalmeet.eu/

Please contact us with questions so that we can guide your design effort.
Updates

Hello designers,

The following information is added to help guide the design process:

1.  For the text dialogue below the landing page, please assume the following word count:
"why are we making dad harbor?": 250 words
"who are we?" 200 words
"what's the deal with the penguin logo?" 300 words

For the social media links, please see http://www.gravelplumbs.com/
Notice the floating "social" bar that is always to the right.  This is the concept we are going for, please try to implement this as you see fit. 

Target Market(s)

Fathers of young children ages 0-6 years old.

Industry/Entity Type

Product

Font styles to use
Sans Serif

Requirements
Must have
• Clean lines, minimal design concept

Incorporation of our logo (see attached document)

Header content is static for all views after landing page, see example

This page WILL be responsive, please keep that in mind when designing
The timeline bar should be to the left, with the timeline bar’s “milestones” also being responsive.

Designer is free to suggest font types, but any fonts used must be royalty-free and web-optimized. We request a minimum number of font types as well as fonts that load relatively fast. We reinforce that visually appealing typography is a significant factor in the winning design choice.

While we are not expecting the winning design to include code, please keep in mind that the final implementation needs to be optimized for desktop, tablet, and mobile platforms.

If you are using stock photography that is not generated by you, please provide where/how we can obtain imagery, as well as price.

All custom graphics must be available in original formats; Photoshop/GIMP layered files for layout design, and vector formats for logos, icons and other graphical elements.

Please incorporate “Blue” into design elements as you see fit, as the RGB 67 74 169 Blue is the primary color used in our brand. The complement to this blue is 255 202 0, a brownish orange. Feel free to use this color as well, although please keep it to a lesser amount.

Background color is your choice, do not feel the need to use the grey.
Should not have
• Excessive graphical content such that it affects loading times

Excessive use of too many font types such that it affects loading times

```html
<!DOCTYPE html>
<html lang="en">
<head>
<meta charset="utf-8">
<title>DadHarbor – Home</title>
<link rel="stylesheet" href="https://fonts.googleapis.com/css2?family=Oswald:wght@400;500&family=PT+Sans:wght@400;700&display=swap">
<style>
  :root{
    --brand-blue:#434aa9;
    --headline-blue:#6470bb;
    --accent-orange:#f7931e;
    --count-orange:#e0660d;
    --ink:#333333;
    --ink-soft:#444444;
    --line:#d6d6d6;
    --page:#ffffff;
  }
  *{box-sizing:border-box;margin:0;padding:0}
  html,body{width:1200px;height:1080px;overflow:hidden;background:var(--page);font-family:"PT Sans",sans-serif;color:var(--ink)}
  .canvas{position:relative;width:1200px;height:1080px}

  /* header */
  .site-header{position:absolute;left:0;top:0;width:1200px;height:165px;border-top:2px solid var(--brand-blue);
    background:linear-gradient(#ffffff,#f3f3f3);box-shadow:0 2px 5px rgba(0,0,0,.12)}
  .brand{position:absolute;left:115px;top:112px;display:flex;align-items:center;gap:8px}
  .brand-mark{width:22px;height:22px;border-radius:50%;background:var(--brand-blue)}
  .brand-name{font-weight:700;font-size:22px;color:var(--brand-blue);letter-spacing:.5px}
  .welcome{position:absolute;left:282px;top:28px;font-family:"Oswald",sans-serif;font-weight:500;font-size:38px;color:var(--headline-blue);letter-spacing:.3px}
  .score{position:absolute;left:290px;top:105px;font-size:17px;color:var(--ink)}
  .search{position:absolute;left:504px;top:100px;width:334px;height:34px;border:1px solid #bdbdbd;border-radius:4px;background:#fff;overflow:hidden}
  .search svg{position:absolute;left:14px;top:8px}
  .search-input{position:absolute;left:44px;top:9px;font-size:12px;color:#999}
  .search-go{position:absolute;right:0;top:0;width:41px;height:32px;background:var(--accent-orange);color:#fff;font-size:12px;text-align:center;line-height:32px}
  .account-links{position:absolute;left:891px;top:104px;font-size:15px;color:var(--ink)}
  .account-links span{margin:0 8px}

  /* side panels */
  .panel{position:absolute;top:193px;width:222px;height:298px;background:var(--brand-blue);border-radius:5px;box-shadow:0 0 0 2px #d9dbef}
  .panel-title{position:absolute;left:8px;top:12px;color:#fff;font-weight:700;font-size:17px}
  .panel-body{position:absolute;left:6px;top:48px;width:210px;height:244px;background:#fff;border-radius:5px}
  .panel-list{list-style:none;position:absolute;left:19px;top:17px}
  .panel-list li{height:30px;font-size:14px;color:var(--ink-soft);display:flex;align-items:center;gap:10px}
  .check{width:13px;height:13px;border:1px solid #a8a8a8;background:linear-gradient(#fff,#e6e6e6)}
  .bullet{width:11px;height:11px;background:var(--brand-blue);border-radius:2px;position:relative}
  .bullet::after{content:"";position:absolute;left:4px;top:2.5px;border-left:4px solid #fff;border-top:3px solid transparent;border-bottom:3px solid transparent}
  .milestones{left:110px}
  .sort{left:881px}

  /* content cards */
  .card{position:absolute;width:214px}
  .card-media{position:relative;width:214px;height:173px;border:2px solid #dcdcdc;border-radius:6px;overflow:hidden}
  .card-media .art{position:absolute;inset:0}
  .art-toy{background:linear-gradient(160deg,#f1f1f1 0%,#5fd03a 35%,#46b7d2 55%,#d8b48c 75%,#ececec 100%)}
  .art-kit{background:linear-gradient(135deg,#f0c6d0 0%,#e64a3f 40%,#f3f3f3 60%,#f49a3c 85%,#6fa2e0 100%)}
  .art-bottles{background:linear-gradient(90deg,#cfd3d6 0%,#f4f6f7 30%,#e2eef0 55%,#f7f9fa 75%,#c9cfd2 100%)}
  .card-band{position:absolute;left:0;bottom:0;width:100%;height:42px;background:rgba(40,40,40,.72);display:flex;align-items:center;justify-content:space-between;padding:0 10px 0 16px}
  .card-type{color:#fff;font-size:18px}
  .card-meta{display:flex;justify-content:space-between;align-items:center;margin:13px 4px 0 8px}
  .stars{display:flex;gap:4px}
  .count{font-size:13px;color:var(--count-orange)}
  .card-text{margin:12px 0 0 7px;font-size:13px;line-height:16px;color:var(--ink)}

  .more{position:absolute;left:488px;top:870px;width:247px;height:55px;background:var(--brand-blue);border:3px solid #d6d8ea;border-radius:4px;
    color:#fff;font-family:"Oswald",sans-serif;font-size:24px;font-variant:small-caps;text-align:center;line-height:47px;letter-spacing:.5px}

  /* footer */
  .site-footer{position:absolute;left:0;top:978px;width:1200px;height:102px;background:var(--brand-blue)}
  .social{position:absolute;left:164px;top:43px;display:flex;gap:12px;list-style:none}
  .social li{width:26px;height:26px;border-radius:3px;border:1px solid rgba(255,255,255,.35)}
  .social .s1{background:#3b5a98}.social .s2{background:#4fc3ee}.social .s3{background:#3a3a3a}
  .social .s4{background:#f29a2e}.social .s5{background:#c8201d}.social .s6{background:#7d95ab}
  .legal{position:absolute;right:169px;top:28px;text-align:right;color:#fff;font-size:13px;line-height:21px}
</style>
</head>
<body>
<div class="canvas">

  <header class="site-header">
    <div class="brand"><span class="brand-mark"></span><span class="brand-name">DADHARBOR</span></div>
    <h1 class="welcome">Welcome Owen, what would you like to do today?</h1>
    <p class="score">Super Dad Score: 10,500</p>
    <div class="search">
      <svg width="18" height="18" viewBox="0 0 18 18"><circle cx="7" cy="7" r="5" fill="none" stroke="#9a9a9a" stroke-width="2"/><line x1="11" y1="11" x2="16" y2="16" stroke="#9a9a9a" stroke-width="2.5"/></svg>
      <span class="search-input">Search</span>
      <span class="search-go">GO</span>
    </div>
    <nav class="account-links">My Account<span>|</span>Logout</nav>
  </header>

  <aside class="panel milestones">
    <h2 class="panel-title">Prepare For The Baby Arrival</h2>
    <div class="panel-body">
      <ul class="panel-list">
        <li><span class="check"></span>Buy a Crib</li>
        <li><span class="check"></span>Assemble The Crib</li>
        <li><span class="check"></span>Buy A Stroller</li>
        <li><svg class="check" viewBox="0 0 13 13" style="border:1px solid #a8a8a8"><path d="M2 6l3 3 6-7" fill="none" stroke="#434aa9" stroke-width="1.6"/></svg>Buy a Carseat</li>
        <li><span class="check"></span>Install a Carseat</li>
        <li><span class="check"></span>Learn to hold a Baby</li>
        <li><span class="check"></span>Set a Feeding Schedule</li>
      </ul>
    </div>
  </aside>

  <aside class="panel sort">
    <h2 class="panel-title">Sort By:</h2>
    <div class="panel-body">
      <ul class="panel-list">
        <li><span class="bullet"></span>Most Recent</li>
        <li><span class="bullet"></span>Most popular</li>
        <li><span class="bullet"></span>Articles only</li>
        <li><span class="bullet"></span>Products only</li>
      </ul>
    </div>
  </aside>

  <svg width="0" height="0" style="position:absolute">
    <defs>
      <symbol id="star" viewBox="0 0 20 20"><path d="M10 1l2.6 5.9 6.4.6-4.8 4.3 1.4 6.3L10 14.8 4.4 18.1l1.4-6.3L1 7.5l6.4-.6z" fill="#434aa9"/></symbol>
      <symbol id="cart" viewBox="0 0 32 28"><path d="M1 3h5l4 15h17l3-11H8" fill="none" stroke="#d8d8d8" stroke-width="2"/><path d="M10 9h19M11 13h17" stroke="#d8d8d8" stroke-width="1.2"/><circle cx="12" cy="23" r="2.4" fill="#d8d8d8"/><circle cx="25" cy="23" r="2.4" fill="#d8d8d8"/></symbol>
    </defs>
  </svg>

  <article class="card" style="left:373px;top:199px">
    <div class="card-media"><div class="art art-toy" role="img" aria-label="Photo of a wooden turtle baby toy with a green shell"></div>
      <div class="card-band"><span class="card-type">Article</span><svg width="32" height="28"><use href="#cart"/></svg></div></div>
    <div class="card-meta"><div class="stars"><svg width="17" height="17"><use href="#star"/></svg><svg width="17" height="17"><use href="#star"/></svg><svg width="17" height="17"><use href="#star"/></svg><svg width="17" height="17"><use href="#star"/></svg><svg width="17" height="17"><use href="#star"/></svg></div><span class="count">3,121 Ratings</span></div>
    <p class="card-text">Sed ut perspiciatis unde omnis iste natus error voluptatem accusantium doloremque laudantium, totam aperiam, eaque ipsa quae.ab illo inventore veritatis et quasi architecto .</p>
  </article>

  <article class="card" style="left:624px;top:199px">
    <div class="card-media"><div class="art art-kit" role="img" aria-label="Photo of a colourful bundle of baby food pouches and blankets"></div>
      <div class="card-band"><span class="card-type">Product</span><svg width="32" height="28"><use href="#cart"/></svg></div></div>
    <div class="card-meta"><div class="stars"><svg width="17" height="17"><use href="#star"/></svg><svg width="17" height="17"><use href="#star"/></svg><svg width="17" height="17"><use href="#star"/></svg><svg width="17" height="17"><use href="#star"/></svg><svg width="17" height="17"><use href="#star"/></svg></div><span class="count" style="margin-right:20px">9,102 likes</span></div>
    <p class="card-text">Sed ut perspiciatis unde omnis iste natus error voluptatem accusantium doloremque laudantium, totam aperiam, eaque ipsa quae.ab illo inventore veritatis et quasi architecto .</p>
  </article>

  <article class="card" style="left:373px;top:530px">
    <div class="card-media"><div class="art art-toy" role="img" aria-label="Photo of a wooden turtle baby toy with a green shell"></div>
      <div class="card-band"><span class="card-type">Article</span><svg width="32" height="28"><use href="#cart"/></svg></div></div>
    <div class="card-meta"><div class="stars"><svg width="17" height="17"><use href="#star"/></svg><svg width="17" height="17"><use href="#star"/></svg><svg width="17" height="17"><use href="#star"/></svg><svg width="17" height="17"><use href="#star"/></svg><svg width="17" height="17"><use href="#star"/></svg></div><span class="count">3,121 Ratings</span></div>
    <p class="card-text">Sed ut perspiciatis unde omnis iste natus error voluptatem accusantium doloremque laudantium, totam aperiam, eaque ipsa quae.ab illo inventore veritatis et quasi architecto .</p>
  </article>

  <article class="card" style="left:624px;top:530px">
    <div class="card-media"><div class="art art-bottles" role="img" aria-label="Photo of white baby care lotion and shampoo bottles"></div>
      <div class="card-band"><span class="card-type">Product</span><svg width="32" height="28"><use href="#cart"/></svg></div></div>
    <div class="card-meta"><div class="stars"><svg width="17" height="17"><use href="#star"/></svg><svg width="17" height="17"><use href="#star"/></svg><svg width="17" height="17"><use href="#star"/></svg><svg width="17" height="17"><use href="#star"/></svg><svg width="17" height="17"><use href="#star"/></svg></div><span class="count" style="margin-right:20px">9,102 likes</span></div>
    <p class="card-text">Sed ut perspiciatis unde omnis iste natus error voluptatem accusantium doloremque laudantium, totam aperiam, eaque ipsa quae.ab illo inventore veritatis et quasi architecto .</p>
  </article>

  <a class="more">More</a>

  <footer class="site-footer">
    <ul class="social" aria-label="Social links">
      <li class="s1"></li><li class="s2"></li><li class="s3"></li><li class="s4"></li><li class="s5"></li><li class="s6"></li>
    </ul>
    <p class="legal">© 2013 dadharbor.com, All Rights Reserved<br>X2</p>
  </footer>

</div>
</body>
</html>
```